RTavenor Business Cards & Letterhead

I have a logo but need a design for some new business cards. We are a Design-Build Firm that specializes in the design and construction of commercial projects.
the cards need to be professional. no cartoon stuff.
i would like to have the cards in AI format so I can update the card as needed. Logo is provided.
Our Address is: 4187 Marlowe Ct. Dornbury, South Dakota 27614

```html
<!DOCTYPE html>
<html lang="en">
<head>
<meta charset="utf-8">
<title>RTavenor Stationery</title>
<link href="https://fonts.googleapis.com/css2?family=Open+Sans:wght@400;600;700;800&display=swap" rel="stylesheet">
<style>
  :root {
    --bg: #d3d5d5;
    --paper: #ffffff;
    --brand-blue: #0f5d9c;
    --brand-blue-deep: #0a3d6b;
    --brand-blue-bright: #1677b8;
    --brand-grey: #6d6e71;
    --wave-grey: #8a8c8e;
    --ink: #1c1c1c;
  }
  * { box-sizing: border-box; margin: 0; padding: 0; }
  html, body { width: 1200px; height: 686px; overflow: hidden; }
  body {
    background: var(--bg);
    font-family: "Open Sans", Arial, sans-serif;
    position: relative;
  }

  /* Letterhead */
  .letterhead {
    position: absolute;
    left: 60px; top: 28px;
    width: 446px; height: 630px;
    background: var(--paper);
    box-shadow: 0 6px 18px rgba(0,0,0,0.18);
    overflow: hidden;
  }
  .wave { position: absolute; left: 0; top: 0; width: 100%; height: 100%; }
  .letterhead-head {
    position: absolute; left: 34px; top: 40px; right: 30px;
  }
  .wordmark {
    display: flex; align-items: center; gap: 8px;
    font-weight: 800; color: var(--brand-grey);
    letter-spacing: 0.02em; text-transform: uppercase;
    white-space: nowrap;
  }
  .wordmark .mark-square {
    width: 0.8em; height: 0.8em; background: var(--brand-blue); border-radius: 2px;
  }
  .letterhead .wordmark { font-size: 27px; }
  .contact-block {
    font-size: 8.5px; line-height: 1.45; color: var(--ink);
    white-space: nowrap;
  }
  .letterhead .contact-block {
    position: absolute; left: 264px; top: 36px;
    border-left: 1px solid var(--ink);
    padding: 2px 0 4px 12px;
  }
  .contact-line { display: flex; align-items: center; gap: 5px; }
  .contact-line svg { width: 8px; height: 8px; flex: none; }
  .contact-line .no-icon { width: 8px; flex: none; }

  /* Business cards */
  .card {
    position: absolute;
    width: 372px; height: 212px;
    border-radius: 12px;
    overflow: hidden;
    box-shadow: 0 6px 16px rgba(0,0,0,0.22);
  }
  .card-front { left: 620px; top: 72px; background: var(--paper); }
  .card-back {
    left: 700px; top: 374px;
    background: radial-gradient(ellipse at 55% 50%, var(--brand-blue-bright) 0%, var(--brand-blue) 45%, var(--brand-blue-deep) 100%);
    display: flex; align-items: center; justify-content: center;
  }
  .card-front .wordmark { position: absolute; left: 22px; top: 18px; font-size: 17px; }
  .card-front .contact-block {
    position: absolute; left: 22px; top: 50px;
    font-size: 7.5px;
  }
  .card-holder {
    position: absolute; right: 20px; top: 80px; text-align: right;
  }
  .holder-name {
    font-size: 14px; font-weight: 700; color: var(--brand-blue-bright);
    text-transform: uppercase; letter-spacing: 0.03em; white-space: nowrap;
  }
  .holder-title { font-size: 8.5px; font-weight: 600; color: var(--ink); margin-top: 2px; }
  .card-back .wordmark { font-size: 30px; color: var(--brand-blue-deep); }
  .card-back .wordmark .mark-square { background: var(--brand-blue-deep); }
</style>
</head>
<body>

<section class="letterhead" aria-label="Letterhead">
  <svg class="wave" viewBox="0 0 446 630" preserveAspectRatio="none" aria-hidden="true">
    <defs>
      <linearGradient id="lh-blue" x1="0" y1="0" x2="1" y2="0.3">
        <stop offset="0" stop-color="#0a3d6b"/>
        <stop offset="0.55" stop-color="#1677b8"/>
        <stop offset="1" stop-color="#0e5a96"/>
      </linearGradient>
    </defs>
    <path d="M0,360 C10,440 50,500 150,535 C60,505 18,450 10,360 Z" fill="#8a8c8e"/>
    <path d="M0,392 C30,480 120,540 260,560 C360,574 420,600 446,630 L0,630 Z" fill="url(#lh-blue)"/>
  </svg>
  <header class="letterhead-head">
    <div class="wordmark"><span class="mark-square"></span>RTavenor</div>
  </header>
  <div class="contact-block">
    <div class="contact-line"><span class="no-icon"></span>4187 Marlowe Ct. Dornbury,</div>
    <div class="contact-line"><span class="no-icon"></span>South Dakota 27614</div>
    <div class="contact-line">
      <svg viewBox="0 0 10 10"><path d="M2,1 L4,1 L4.6,3 L3.4,4 Q4.5,6 6,6.6 L7,5.4 L9,6 L9,8 Q5,9.5 1,2 Z" fill="#0f5d9c"/></svg>
      (312) 555-0148</div>
    <div class="contact-line">
      <svg viewBox="0 0 10 10"><circle cx="5" cy="5" r="4" fill="none" stroke="#0f5d9c" stroke-width="1.2"/><path d="M1,5 H9 M5,1 Q2.5,5 5,9 Q7.5,5 5,1" fill="none" stroke="#0f5d9c" stroke-width="0.8"/></svg>
      www.rtavenor.com</div>
    <div class="contact-line">
      <svg viewBox="0 0 10 10"><rect x="1" y="2" width="8" height="6" fill="#0f5d9c"/><path d="M1,2 L5,5.5 L9,2" fill="none" stroke="#fff" stroke-width="0.8"/></svg>
      RT@RTavenor.com</div>
  </div>
</section>

<section class="card card-front" aria-label="Business card front">
  <svg class="wave" viewBox="0 0 372 212" preserveAspectRatio="none" aria-hidden="true">
    <defs>
      <linearGradient id="bc-blue" x1="0" y1="0" x2="1" y2="0.3">
        <stop offset="0" stop-color="#0a3d6b"/>
        <stop offset="0.6" stop-color="#1677b8"/>
        <stop offset="1" stop-color="#0e5a96"/>
      </linearGradient>
    </defs>
    <path d="M0,118 C6,150 30,170 80,182 C36,168 10,150 5,118 Z" fill="#8a8c8e"/>
    <path d="M0,134 C40,172 120,184 220,192 C300,198 350,204 372,212 L0,212 Z" fill="url(#bc-blue)"/>
  </svg>
  <div class="wordmark"><span class="mark-square"></span>RTavenor</div>
  <div class="contact-block">
    <div class="contact-line"><span class="no-icon"></span>4187 Marlowe Ct. Dornbury,</div>
    <div class="contact-line"><span class="no-icon"></span>South Dakota 27614</div>
    <div class="contact-line">
      <svg viewBox="0 0 10 10"><path d="M2,1 L4,1 L4.6,3 L3.4,4 Q4.5,6 6,6.6 L7,5.4 L9,6 L9,8 Q5,9.5 1,2 Z" fill="#0f5d9c"/></svg>
      (312) 555-0148</div>
    <div class="contact-line">
      <svg viewBox="0 0 10 10"><circle cx="5" cy="5" r="4" fill="none" stroke="#0f5d9c" stroke-width="1.2"/><path d="M1,5 H9 M5,1 Q2.5,5 5,9 Q7.5,5 5,1" fill="none" stroke="#0f5d9c" stroke-width="0.8"/></svg>
      www.rtavenor.com</div>
    <div class="contact-line">
      <svg viewBox="0 0 10 10"><rect x="1" y="2" width="8" height="6" fill="#0f5d9c"/><path d="M1,2 L5,5.5 L9,2" fill="none" stroke="#fff" stroke-width="0.8"/></svg>
      RT@RTavenor.com</div>
  </div>
  <div class="card-holder">
    <div class="holder-name">Rowan Tavenor</div>
    <div class="holder-title">Founder/President</div>
  </div>
</section>

<section class="card card-back" aria-label="Business card back">
  <div class="wordmark"><span class="mark-square"></span>RTavenor</div>
</section>

</body>
</html>
```